New Alcoholic Spiked Seltzer Line

We need a can design for a line of low calorie alcoholic seltzer. This product is a sparkling water and vodka drink with no sugar added in a slim 12 oz can.

This is a lighter, healthier, alternative to the sugary ready-to-drinks on the market. The product contains only 3 ingredients: Vodka, Water and Natural Flavors. It has only 100 calories but still has 5% alcohol, so you don't need to sacrifice alcohol to cut calories.

This product also does not contain any preservatives.

We want this design to communicate the following objectives to the consumer and in this order:

1. Appetizing product
2.Low calorie
3.Communicate the type of beverage (Spiked Seltzer)

The brand name of the product is VELKA.

The flavor of the product needed to be used for the design is Mango-Orange.

Comparable products are:

www.brindlefizzworks.example/
https://www.quorvabubbles.example
https://pelnavo.example/

The designs should not infringe or copy the creative directions of the products mentionned above. They are only given so that you can better understand the type of product we are developing.

Target Market(s)

Young Professional women between the ages of 25 and 44

Industry/Entity Type

Product

Colors

Designer to choose colors to be used in the design.

Requirements
Must have
• Design extendibility, meaning it can be adapted for other flavors.
• This is a new category in the market we are targeting, so consumers must easily be able to identify what type of product this is.

```html
<!DOCTYPE html>
<html lang="en">
<head>
<meta charset="utf-8">
<title>VELKA Spiked Sparkling Seltzer – Mango-Orange Can Label</title>
<link rel="stylesheet" href="https://fonts.googleapis.com/css2?family=Audiowide&family=Orbitron:wght@400&family=Pacifico&family=Lora:wght@400&family=Montserrat:wght@800&display=swap">
<style>
  :root {
    --ink: #000000;
    --paper: #ffffff;
    --steel: #e6e6e6;
    --steel-shade: #6f6f6f;
    --leaf-green: #3aa56b;
    --mango-yellow: #ffe600;
    --orange-deep: #f07a10;
    --fruit-light: #ffc940;
    --fruit-dark: #f08a1c;
  }
  html, body {
    margin: 0;
    width: 1200px;
    height: 1051px;
    overflow: hidden;
    background: var(--paper);
  }
  .label {
    position: absolute;
    left: 412px;
    top: 75px;
    width: 375px;
    height: 900px;
    background: var(--paper);
  }
  .band {
    position: absolute;
    left: 0;
    width: 100%;
    height: 32px;
    background: var(--ink);
  }
  .band--top { top: 0; }
  .band--bottom { bottom: 0; }
  .brand-block {
    position: absolute;
    left: 23px;
    top: 84px;
    width: 327px;
    height: 133px;
    background: var(--ink);
    display: flex;
    align-items: center;
    justify-content: center;
  }
  .brand-name {
    font-family: "Audiowide", sans-serif;
    font-size: 66px;
    color: var(--paper);
    letter-spacing: 2px;
  }
  .claim {
    position: absolute;
    top: 226px;
    width: 100%;
    text-align: center;
    font-family: "Montserrat", sans-serif;
    font-weight: 800;
    font-size: 11.5px;
    color: var(--ink);
    margin: 0;
  }
  .category {
    position: absolute;
    top: 262px;
    width: 100%;
    text-align: center;
    margin: 0;
    font-family: "Orbitron", sans-serif;
    font-size: 27px;
    line-height: 38px;
    letter-spacing: 1px;
    color: var(--steel);
    text-shadow: 1px 1px 0 var(--steel-shade), -1px 0 0 var(--steel-shade), 0 -1px 0 #9a9a9a, 2px 2px 3px rgba(0,0,0,.45);
  }
  .flavor {
    position: absolute;
    left: 0;
    top: 345px;
    width: 375px;
    height: 190px;
  }
  .flavor text {
    font-family: "Pacifico", cursive;
    font-size: 62px;
    paint-order: stroke;
    stroke: var(--ink);
    stroke-width: 12px;
    stroke-linejoin: round;
  }
  .ingredients {
    position: absolute;
    left: -2px;
    top: 550px;
    margin: 0;
    font-family: "Lora", serif;
    font-size: 28px;
    line-height: 29px;
    color: var(--leaf-green);
  }
  .ingredients span { display: block; padding-left: 20px; }
  .ingredients span:first-child { padding-left: 0; }
  .fruit-visual {
    position: absolute;
    left: 0;
    top: 633px;
    width: 100%;
    height: 175px;
    background: radial-gradient(ellipse at 30% 50%, var(--fruit-dark) 0%, var(--fruit-light) 55%, rgba(255,255,255,0) 78%),
                radial-gradient(ellipse at 75% 50%, var(--fruit-light) 0%, #ffd84d 50%, rgba(255,255,255,0) 80%);
  }
  .volume {
    position: absolute;
    top: 830px;
    width: 100%;
    text-align: center;
    margin: 0;
    font-family: "Lora", serif;
    font-size: 15px;
    color: var(--ink);
  }
</style>
</head>
<body>
  <main class="label">
    <div class="band band--top"></div>

    <div class="brand-block">
      <span class="brand-name">VELKA</span>
    </div>

    <p class="claim">LOW-CALORIE SUGAR-FREE</p>

    <p class="category">SPIKED SPARKLING<br>SELTZER IN</p>

    <svg class="flavor" viewBox="0 0 375 190" aria-label="Mango-Orange">
      <defs>
        <linearGradient id="flavor-fill" x1="0" y1="0" x2="0" y2="1">
          <stop offset="0" stop-color="var(--mango-yellow)"/>
          <stop offset="0.55" stop-color="#ffb000"/>
          <stop offset="1" stop-color="var(--orange-deep)"/>
        </linearGradient>
      </defs>
      <text x="190" y="70" text-anchor="middle" fill="url(#flavor-fill)" transform="rotate(-3 190 70)">Mango-</text>
      <text x="195" y="150" text-anchor="middle" fill="url(#flavor-fill)" transform="rotate(-3 195 150)">Orange</text>
    </svg>

    <p class="ingredients"><span>vodka+water</span><span>+natural flavors</span></p>

    <div class="fruit-visual" role="img" aria-label="Photo of whole and halved oranges with leaves next to a ripe mango and a cubed mango half"></div>

    <p class="volume">5% ALC. /VOL &nbsp;•&nbsp; 12 FL OZ</p>

    <div class="band band--bottom"></div>
  </main>
</body>
</html>
```